Specialised investor in e-mobility and energy wants business card design

We need a business card design that fits our existing corporate design. <The look and feel must be 'sharp'/'clean', dynamic, communicate momentum, professionalism etc (as one would imagine from a firm in the financial sector). We like the idea of a reverse-side of the card that includes the logo, and the name and contact details on the other. We expect the deliverable to be whatever format might be required to be able to get cards printed directly by a service such as kelmo press. Our website is www.zub.capital

```html
<!DOCTYPE html>
<html lang="en">
<head>
<meta charset="utf-8">
<title>Zub Capital – Business Card</title>
<link rel="stylesheet" href="https://fonts.googleapis.com/css2?family=Arimo:wght@400;700&display=swap">
<style>
  :root {
    --page: #e9ebe6;
    --forest: #344f24;
    --forest-deep: #2b431e;
    --lime: #86b548;
    --paper: #ffffff;
    --ink: #3a3a3a;
  }
  * { margin: 0; padding: 0; box-sizing: border-box; }
  html, body { width: 1200px; height: 988px; overflow: hidden; background: var(--page); }
  body { position: relative; font-family: "Arimo", Arial, sans-serif; }

  .card {
    position: absolute;
    left: 220px;
    width: 760px;
    height: 434px;
    border-radius: 28px;
    overflow: hidden;
    box-shadow: 0 6px 18px rgba(0,0,0,.18);
  }

  /* Logo side */
  .card--logo { top: 40px; background: var(--forest); display: flex; align-items: center; justify-content: center; }
  .brand { display: flex; align-items: center; gap: 18px; }
  .brand__dot { width: 22px; height: 22px; border-radius: 50%; background: var(--lime); }
  .brand__name { font-size: 74px; font-weight: 400; letter-spacing: 1px; color: var(--paper); }

  /* Details side */
  .card--details { top: 514px; background: var(--paper); }
  .card--details .brand { position: absolute; left: 64px; top: 168px; gap: 12px; }
  .card--details .brand__dot { width: 14px; height: 14px; }
  .card--details .brand__name { font-size: 44px; color: var(--forest); }

  .divider { position: absolute; left: 372px; top: 66px; width: 1.5px; height: 190px; background: var(--forest); }

  .contact { position: absolute; left: 404px; top: 62px; color: var(--ink); }
  .contact__name { font-size: 28px; font-weight: 700; letter-spacing: .5px; color: var(--forest); line-height: 1; }
  .contact__name span { color: var(--lime); }
  .contact__role { font-size: 15px; margin-top: 4px; }
  .contact__address { font-size: 15px; line-height: 1.3; margin-top: 14px; }
  .contact__list { list-style: none; margin-top: 14px; font-size: 15px; line-height: 1.55; }
  .contact__list li { display: flex; align-items: center; gap: 9px; }
  .contact__list svg { width: 14px; height: 14px; flex: none; }

  .swoosh { position: absolute; left: 0; top: 0; width: 760px; height: 434px; }
</style>
</head>
<body>

  <section class="card card--logo" aria-label="Card front">
    <div class="brand">
      <span class="brand__dot"></span>
      <span class="brand__name">Zub Capital</span>
    </div>
  </section>

  <section class="card card--details" aria-label="Card back">
    <svg class="swoosh" viewBox="0 0 760 434" aria-hidden="true">
      <path d="M430,434 C560,364 650,314 760,244 L760,252 C655,322 570,372 468,434 Z" fill="var(--lime)"/>
      <path d="M480,434 C585,376 665,330 760,262 L760,434 Z" fill="var(--forest)"/>
    </svg>

    <div class="brand">
      <span class="brand__dot"></span>
      <span class="brand__name">Zub Capital</span>
    </div>

    <div class="divider"></div>

    <div class="contact">
      <h1 class="contact__name">MARTIN <span>KERROW</span></h1>
      <p class="contact__role">Director/Founder</p>
      <p class="contact__address">1234 Street Name<br>Country Name AB 5748</p>
      <ul class="contact__list">
        <li>
          <svg viewBox="0 0 14 14"><circle cx="7" cy="7" r="7" fill="var(--lime)"/><path d="M4.3 3.6l1.4-.3.7 1.8-.9.6a5 5 0 0 0 2.8 2.8l.6-.9 1.8.7-.3 1.4C7.2 9.9 4.1 6.8 4.3 3.6z" fill="#fff"/></svg>
          123-555-0184
        </li>
        <li>
          <svg viewBox="0 0 14 14"><circle cx="7" cy="7" r="7" fill="var(--lime)"/><rect x="3.5" y="4.5" width="7" height="5" fill="#fff"/><path d="M3.5 4.5L7 7.3l3.5-2.8" fill="none" stroke="var(--lime)" stroke-width=".9"/></svg>
          info@zub.capital
        </li>
        <li>
          <svg viewBox="0 0 14 14"><circle cx="7" cy="7" r="7" fill="var(--lime)"/><circle cx="7" cy="7" r="3.6" fill="none" stroke="#fff" stroke-width="1"/><path d="M3.4 7h7.2M7 3.4c-1.6 2-1.6 5.2 0 7.2M7 3.4c1.6 2 1.6 5.2 0 7.2" fill="none" stroke="#fff" stroke-width=".8"/></svg>
          www.zub.capital
        </li>
      </ul>
    </div>
  </section>

</body>
</html>
```